Letterhead That Inspires Trust

Harbor Deed Remedies, LLC, (HDR) fixes technical problems with property deeds. The problems usually surface when someone tries to buy, sell or mortgage a piece of real estate and one of the lawyers involved find a title defect (a lien, an undischarged mortgage, a deceased person still on the title, unpaid taxes, etc.). HDR then gets involved and often has to contact prior property owners to get them to sign paperwork fixing the problem. We need a letterhead that will a) convey the seriousness of what we are trying to do, b) cause the recipients of our letters to recognize the importance of what are trying to do, and c) convey that we are a established and trustworthy company. We want it to include an image that suggests we are a problem solving company. Attached is an image we think might work; you can use it or not. In addition to our name (Harbor Deed Remedies, LLC), the letterhead must include our address and phone number: 418 Alder Lane, Suite 207, Wexmoor, RI 02911 (401) 555-3827. We are thinking something straightforward without unnecessary colors or graphics.

```html
<!DOCTYPE html>
<html lang="en">
<head>
<meta charset="utf-8">
<title>Harbor Deed Remedies, LLC — Letterhead</title>
<link rel="stylesheet" href="https://fonts.googleapis.com/css2?family=Open+Sans:wght@400;600;700&display=swap">
<style>
  :root {
    --backdrop: #b1b2b1;
    --paper: #fafafa;
    --brand-green: #0f9447;
    --body-text: #6d6d6d;
    --contact-text: #3a3a3a;
    --footer-band: #2b2a28;
    --signature-ink: #cfe5f4;
  }
  * { margin: 0; padding: 0; box-sizing: border-box; }
  html, body {
    width: 1200px; height: 950px; overflow: hidden;
    background: var(--backdrop);
    font-family: "Open Sans", Arial, sans-serif;
  }
  .letterhead {
    position: absolute; left: 306px; top: 58px;
    width: 589px; height: 834px;
    background: var(--paper);
  }
  .brand {
    position: absolute; left: 57px; top: 63px;
    display: flex; align-items: center; gap: 9px;
  }
  .brand-mark { width: 14px; height: 14px; background: var(--brand-green); }
  .brand-name {
    font-size: 17px; font-weight: 600; color: var(--brand-green);
    letter-spacing: 0.2px;
  }
  .contact {
    position: absolute; left: 390px; top: 50px;
    list-style: none; font-size: 10.4px; line-height: 13.6px;
    color: var(--contact-text);
  }
  .contact li { display: flex; align-items: flex-start; }
  .contact svg { width: 9px; height: 9px; margin: 2px 8px 0 0; flex: none; fill: var(--brand-green); }
  .contact .street-address { display: block; }
  .letter-body {
    position: absolute; left: 57px; top: 203px; width: 472px;
    font-size: 8.8px; line-height: 15.1px; color: var(--body-text);
  }
  .salutation { margin-bottom: 30px; }
  .letter-body p.paragraph { text-align: justify; margin-bottom: 15px; }
  .sign-off {
    position: absolute; left: 57px; top: 565px;
    font-size: 8.8px; color: var(--body-text);
  }
  .signer-label { font-weight: 700; }
  .signature {
    width: 143px; height: 32px; margin: 10px 0 6px;
    background: var(--signature-ink); border-radius: 4px;
  }
  .footer-band {
    position: absolute; left: 0; bottom: 0; width: 100%; height: 8px;
    background: var(--footer-band);
  }
</style>
</head>
<body>
  <main class="letterhead">
    <header>
      <div class="brand">
        <span class="brand-mark"></span>
        <span class="brand-name">Harbor Deed Remedies, LLC</span>
      </div>
      <ul class="contact">
        <li>
          <svg viewBox="0 0 10 10" aria-hidden="true"><path d="M1 3.2C1 2 3 1.5 5 1.5S9 2 9 3.2L7.6 4 6.8 3.2H3.2L2.4 4ZM2.5 5h5l1 3.5h-7Z"/></svg>
          <span>(401) 555-3827</span>
        </li>
        <li>
          <svg viewBox="0 0 10 10" aria-hidden="true"><path d="M1 2.5h8v5H1Zm.8.6L5 5.6l3.2-2.5Z" fill-rule="evenodd"/></svg>
          <span>office@harbordeedremedies.com</span>
        </li>
        <li>
          <svg viewBox="0 0 10 10" aria-hidden="true"><path d="M5 .5a3.3 3.3 0 0 1 3.3 3.3C8.3 6.3 5 9.5 5 9.5S1.7 6.3 1.7 3.8A3.3 3.3 0 0 1 5 .5Zm0 2a1.3 1.3 0 1 0 0 2.6 1.3 1.3 0 0 0 0-2.6Z" fill-rule="evenodd"/></svg>
          <span class="street-address">418 Alder Lane, Suite 207,<br>Wexmoor, RI 02911</span>
        </li>
      </ul>
    </header>

    <section class="letter-body">
      <p class="salutation">Dear Sir,</p>
      <p class="paragraph">Lorem Ipsum is simply dummy text of the printing and typesetting industry. Lorem Ipsum has been the industry's standard dummy text ever since the 1500s, when an unknown printer took a galley of type and scrambled it to make a type specimen book. It has survived not only five centuries, but also the leap into electronic typesetting, remaining essentially unchanged. It was popularised in the 1960s with the release of transfer sheets containing Lorem Ipsum passages, and more recently with desktop publishing software like Quillset Layout including versions of Lorem Ipsum.</p>
      <p class="paragraph">Lorem Ipsum is simply dummy text of the printing and typesetting industry. Lorem Ipsum has been the industry's standard dummy text ever since the 1500s, when an unknown printer took a galley of type and scrambled it to make a type specimen book. It has survived not only five centuries, but also the leap into electronic typesetting, remaining essentially unchanged. It was popularised in the 1960s with the release of transfer sheets containing Lorem Ipsum passages, and more recently with desktop publishing software like Quillset Layout including versions of Lorem Ipsum.</p>
      <p class="paragraph">Lorem Ipsum is simply dummy text of the printing and typesetting industry. Lorem Ipsum has been the industry's standard dummy text ever since the 1500s, when an unknown printer took a galley of type and scrambled it to make a type specimen book.</p>
    </section>

    <footer class="sign-off">
      <p class="signer-label">Your Name</p>
      <div class="signature" role="img" aria-label="Handwritten signature of Martin Oakes in blue ink"></div>
      <p class="signer-title">CEO &nbsp;|&nbsp; Owner</p>
    </footer>

    <div class="footer-band"></div>
  </main>
</body>
</html>
```